50's-style gig poster for a birthday bash

My wife was born in 1957 and is turning 57 next month. I'm throwing a surprise party for her, and thought it would be fun to have a 18x24 poster printed and framed for the event. Attached is a poster from a Rufus Kendrick gig in 1957. I'd like something like this, with a tinted B&W head shot of my wife, with similar fonts and background color schemes. The copy will be LORNA at the top (where the name RUFUS appears), with 57X57 under it, and the word Celebration where the word Quartet currently appears. The rest of the copy will be provided to you. Thanks for your interest and I look forward to working with you.

```html
<!DOCTYPE html>
<html lang="en">
<head>
<meta charset="UTF-8">
<title>LORNA 57 x 57 Celebration</title>
<link href="https://fonts.googleapis.com/css2?family=Josefin+Sans:wght@700&family=Lobster+Two:ital,wght@1,700&family=Montserrat:ital,wght@0,700;1,500&family=Abril+Fatface&family=Alfa+Slab+One&display=swap" rel="stylesheet">
<style>
  :root {
    --paper: #e8dcc0;
    --cream: #f2ead8;
    --blue: #1f4590;
    --red: #e01b2a;
    --ink: #1e1a17;
    --shadow: #2a2522;
  }
  * { margin: 0; padding: 0; box-sizing: border-box; }
  html, body { width: 834px; height: 1200px; overflow: hidden; background: var(--paper); }
  .poster {
    position: relative;
    width: 834px;
    height: 1200px;
    overflow: hidden;
    background: radial-gradient(ellipse at center, #efe4ca 0%, var(--paper) 60%, #dccdaa 100%);
  }
  .stripe { position: absolute; top: 35px; bottom: 0; }
  .stripe--blue { background: var(--blue); }
  .stripe--red { background: var(--red); }
  .s1 { left: 36px; width: 137px; }
  .s2 { left: 192px; width: 138px; }
  .s3 { left: 347px; width: 138px; }
  .s4 { left: 501px; width: 138px; }
  .s5 { left: 658px; width: 136px; }

  .headline-glyph {
    position: absolute;
    display: flex;
    justify-content: center;
    align-items: center;
    font-family: "Josefin Sans", sans-serif;
    font-weight: 700;
    color: var(--cream);
    text-shadow: 5px 5px 0 var(--shadow);
    line-height: 1;
  }
  .name-row { top: 40px; height: 140px; font-size: 168px; }
  .age-row { top: 192px; height: 140px; font-size: 168px; }
  .age-row .times { font-size: 96px; }
  .c1 { left: 20px; width: 169px; }
  .c2 { left: 176px; width: 170px; }
  .c3 { left: 331px; width: 170px; }
  .c4 { left: 485px; width: 170px; }
  .c5 { left: 642px; width: 168px; }

  .portrait {
    position: absolute;
    left: 62px;
    top: 394px;
    width: 340px;
    height: 402px;
    background: var(--cream);
    border: 3px solid var(--ink);
    padding: 14px;
    transform: rotate(-2deg);
  }
  .portrait-fill {
    width: 100%;
    height: 100%;
    background: linear-gradient(160deg, #d9d7d2 0%, #9d9993 55%, #5f5b56 100%);
  }

  .celebration {
    position: absolute;
    left: 392px;
    top: 350px;
    width: 380px;
    text-align: center;
    font-family: "Lobster Two", cursive;
    font-style: italic;
    font-weight: 700;
    font-size: 74px;
    color: var(--cream);
    text-shadow: 4px 4px 0 var(--shadow);
    transform: rotate(-4deg);
  }
  .lineup {
    position: absolute;
    left: 398px;
    top: 466px;
    width: 352px;
    text-align: center;
    color: var(--cream);
    text-shadow: 2px 2px 0 var(--shadow);
  }
  .lineup-label {
    font-family: "Montserrat", sans-serif;
    font-style: italic;
    font-weight: 500;
    font-size: 23px;
    line-height: 30px;
  }
  .lineup-act {
    font-family: "Montserrat", sans-serif;
    font-weight: 700;
    font-size: 25px;
    line-height: 42px;
  }

  .date-oval {
    position: absolute;
    left: 464px;
    top: 734px;
    width: 244px;
    height: 160px;
  }
  .date-text {
    position: absolute;
    left: 464px;
    top: 748px;
    width: 244px;
    text-align: center;
    color: var(--blue);
  }
  .date-title {
    font-family: "Abril Fatface", serif;
    font-size: 30px;
    line-height: 32px;
  }
  .date-detail {
    margin-top: 8px;
    font-family: "Montserrat", sans-serif;
    font-weight: 700;
    font-size: 17px;
    line-height: 22px;
  }

  .tag {
    position: absolute;
    left: 48px;
    top: 880px;
    width: 268px;
    height: 42px;
    background: var(--cream);
    border: 2px solid var(--ink);
    display: flex;
    align-items: center;
    justify-content: center;
    font-family: "Montserrat", sans-serif;
    font-weight: 700;
    font-size: 21px;
    color: var(--blue);
    transform: rotate(-1deg);
  }

  .headliner {
    position: absolute;
    left: 0;
    top: 940px;
    width: 834px;
    text-align: center;
    font-family: "Lobster Two", cursive;
    font-style: italic;
    font-weight: 700;
    font-size: 66px;
    color: var(--cream);
    text-shadow: 4px 4px 0 var(--shadow);
  }

  .venue {
    position: absolute;
    left: 68px;
    top: 1046px;
    width: 698px;
    height: 120px;
    background: var(--cream);
    border: 3px solid var(--ink);
    text-align: center;
    color: var(--ink);
  }
  .venue-name {
    font-family: "Alfa Slab One", serif;
    font-size: 58px;
    letter-spacing: 3px;
    line-height: 76px;
    margin-top: 4px;
  }
  .venue-address {
    font-family: "Montserrat", sans-serif;
    font-weight: 700;
    font-size: 19px;
  }
</style>
</head>
<body>
<div class="poster">
  <div class="stripe stripe--blue s1"></div>
  <div class="stripe stripe--red s2"></div>
  <div class="stripe stripe--blue s3"></div>
  <div class="stripe stripe--red s4"></div>
  <div class="stripe stripe--blue s5"></div>

  <h1 aria-label="LORNA">
    <span class="headline-glyph name-row c1">L</span>
    <span class="headline-glyph name-row c2">O</span>
    <span class="headline-glyph name-row c3">R</span>
    <span class="headline-glyph name-row c4">N</span>
    <span class="headline-glyph name-row c5">A</span>
  </h1>
  <div aria-label="57 x 57">
    <span class="headline-glyph age-row c1">5</span>
    <span class="headline-glyph age-row c2">7</span>
    <span class="headline-glyph age-row c3"><span class="times">x</span></span>
    <span class="headline-glyph age-row c4">5</span>
    <span class="headline-glyph age-row c5">7</span>
  </div>

  <div class="portrait">
    <div class="portrait-fill" role="img" aria-label="Tinted black and white head shot of Lorna smiling"></div>
  </div>

  <div class="celebration">Celebration</div>
  <div class="lineup">
    <p class="lineup-label">Featuring:</p>
    <p class="lineup-act">The Halvorsens</p>
    <p class="lineup-act">The Winthrops</p>
    <p class="lineup-act">The Marlow-Ashbys</p>
    <p class="lineup-act">The Penderells</p>
    <p class="lineup-act">The Castlemans</p>
  </div>

  <svg class="date-oval" viewBox="0 0 244 160" aria-hidden="true">
    <ellipse cx="122" cy="80" rx="119" ry="77" fill="#f2ead8" stroke="#1e1a17" stroke-width="3"/>
  </svg>
  <div class="date-text">
    <p class="date-title">One Night<br>Only</p>
    <p class="date-detail">April 4, 2014<br>6 PM</p>
  </div>

  <div class="tag">One Night Only</div>

  <div class="headliner">The Chirps &amp; Dale Voss</div>

  <div class="venue">
    <p class="venue-name">BISTRO MARCEL</p>
    <p class="venue-address">418 Cedar Lane, Paso Robles, California</p>
  </div>
</div>
</body>
</html>
```